Harborline Lending and Capital. We provide MOSTLY residential home mortgages in Florida AND commercial loans for investment properties throughout the United states.
I would love to emulate so of the lender sites that are available on the internet but I would like to have the site as popular as possible for SEO purposes. Clients can already click the link to take them to the mortgage application where they can complete that and upload documents. If you could polish that up for me that would be great. I can also provide you with great detail on loan programs that are currently being offered. WE OFFER ALL MORTGAGE LENDING PRODUCTS. I would also like to add something in reference to the rate but I don't think it's legal to actually state or promise a rate for mortgage since they vary based on loan type, client and other criteria...

On the Harborline real estate site I would like to add a link or some way for clients to be able to put in credit card information to render services ...

Please let me know what you need from me

Thank you !!

Current link to site to improve and code

https://harborlinelendingandcapital.example/

Industry/Entity Type

Residential and commmercial lending

Coding

Coded - Design and coding required

Number of Pages Required

2 page

Requirements
Must have
• Love to integrate Mortgage interest rates even if general
Nice to have
• Link to fill out mortgage application via Quorvel LPX software

```html
<!DOCTYPE html>
<html lang="en">
<head>
<meta charset="utf-8">
<title>Harborline Lending and Capital</title>
<link href="https://fonts.googleapis.com/css2?family=Poppins:wght@400;500;600;700;800&family=Montserrat:wght@400;500;600&display=swap" rel="stylesheet">
<style>
:root{
  --forest:#173d17;
  --forest-deep:#112e11;
  --lime:#8dbd30;
  --lime-dark:#6e9a22;
  --cream:#f2f5e6;
  --ink:#222;
  --muted:#555;
  --white:#fff;
}
*{box-sizing:border-box;margin:0;padding:0}
html,body{width:1200px;height:4612px;overflow:hidden}
body{font-family:"Poppins",sans-serif;color:var(--ink);background:var(--white);position:relative}
a{text-decoration:none}
.abs{position:absolute}
.eyebrow{font-family:"Montserrat",sans-serif;letter-spacing:4px;font-size:16px;color:#444;text-transform:uppercase}
.sec-title{font-weight:800;color:var(--forest);font-size:36px;line-height:1.3;text-transform:uppercase;text-shadow:0 2px 0 rgba(0,0,0,.12)}
.circle{border-radius:50%;display:flex;align-items:center;justify-content:center}
.social{width:37px;height:37px;background:var(--lime);border-radius:50%;display:inline-block;margin-right:8px;vertical-align:middle}
.social.dark{background:var(--forest)}
.photo{border-radius:30px}
/* header */
.topbar{top:0;left:0;width:1200px;height:90px;background:var(--white)}
.brand-badge{left:90px;top:10px;width:150px;height:150px;border-radius:50%;background:var(--white);z-index:3}
.brand-mark{left:115px;top:32px;width:100px;height:100px;border-radius:50%;background:var(--forest);z-index:4}
.brand-name{left:253px;top:86px;font-size:9.5px;font-weight:700;color:var(--forest);z-index:4;line-height:1.6}
.brand-name span{display:block;font-weight:400;letter-spacing:4.5px;color:#666}
.nav{left:546px;top:90px;width:654px;height:60px;background:var(--lime);display:flex;align-items:center;gap:44px;padding-left:54px}
.nav a{color:var(--white);font-size:13px;font-weight:600}
.nav a.current{border-bottom:2px solid var(--white);padding-bottom:3px}
.contact-mini{font-size:9px;color:#555;line-height:1.3}
.contact-mini b{display:block;font-size:19px;color:var(--ink);font-weight:600}
/* hero */
.hero{top:150px;left:0;width:1200px;height:522px;background:var(--forest)}
.hero-photo{left:546px;top:0;width:654px;height:522px;background:linear-gradient(135deg,#c9c5bc,#8d8a84 55%,#3f3f3f);clip-path:polygon(8% 0,100% 0,100% 100%,0 100%,12% 50%)}
.hero-label{left:82px;top:120px;color:var(--lime);font-size:14px;font-weight:600;line-height:1.75;width:420px}
.hero h1{position:absolute;left:82px;top:168px;color:var(--white);font-weight:800;font-size:60px;line-height:1}
.hero h2{position:absolute;left:82px;top:238px;color:var(--white);font-weight:800;font-size:45px;line-height:1}
.hero h3{position:absolute;left:82px;top:300px;color:var(--white);font-weight:600;font-size:26px}
.hero-cta{left:84px;top:351px;width:466px;height:42px;border-radius:21px;background:var(--white);color:var(--lime-dark);font-size:13px;font-weight:700;display:flex;align-items:center;justify-content:center;box-shadow:0 4px 0 var(--lime)}
.scroll-bump{left:560px;top:640px;width:80px;height:40px;border-radius:40px 40px 0 0;background:var(--white)}
/* about */
.vline{width:2px;background:var(--forest)}
.about-text{left:663px;top:895px;width:430px;font-size:14.5px;line-height:32px;color:#444}
.about-text p{margin-bottom:18px}
.ticks{list-style:none}
.ticks li{font-size:14.5px;font-weight:500;color:var(--forest);line-height:32px;display:flex;align-items:center;gap:12px}
.tick{width:13px;height:13px;border:2px solid var(--lime);border-radius:50%;position:relative}
.tick:after{content:"";position:absolute;left:2px;top:2px;width:5px;height:5px;background:var(--lime);border-radius:50%}
.btn-dark{background:var(--forest);color:var(--white);font-weight:600;font-size:15px;border-radius:22px;display:flex;align-items:center;justify-content:center;box-shadow:0 4px 0 var(--lime)}
/* products */
.products{top:1470px;left:0;width:1200px;height:828px;background:linear-gradient(180deg,#7ba42a,#6f9a23 60%,#628c1e)}
.card{width:313px;height:207px;border-radius:18px;background:rgba(255,255,255,.12);padding:28px 26px;color:var(--white)}
.card.active{background:var(--white);color:var(--muted)}
.card h4{font-size:15px;font-weight:700;margin:14px 0 8px;text-transform:uppercase;color:var(--white)}
.card.active h4{color:var(--lime-dark)}
.card p{font-size:12px;line-height:24px}
/* rates */
.rate-icon{width:68px;height:68px;border-radius:50%;background:var(--forest);border:3px solid var(--lime)}
.rate-num{font-size:38px;font-weight:700;color:var(--forest);line-height:1}
.rate-num sup{font-size:16px}
.rate-label{font-size:15px;font-weight:600;color:var(--ink)}
.rate-copy{font-size:14px;line-height:28px;color:#555;width:430px}
/* properties */
.properties{top:2977px;left:0;width:1200px;height:677px;background:var(--cream)}
.prop{width:317px;height:430px;border-radius:20px;overflow:hidden}
.prop-tag{position:absolute;left:16px;right:16px;bottom:16px;height:68px;border-radius:10px;background:var(--forest);display:flex;align-items:center;gap:22px;padding-left:18px;color:var(--white)}
.prop-tag.light{background:var(--white);color:var(--ink)}
.pin-box{width:52px;height:52px;border-radius:8px;background:var(--lime);display:flex;align-items:center;justify-content:center}
.prop-tag b{display:block;font-size:15px;font-weight:600}
.prop-tag a{font-size:11px;color:inherit;font-weight:600;text-decoration:underline}
.prop-tag.light a{color:var(--lime-dark)}
.arrow-btn{width:34px;height:34px;border-radius:50%}
/* contact */
.contact{top:3654px;left:0;width:1200px;height:582px;background:linear-gradient(180deg,#0f2c10,#163d16 60%,#1d4a1c)}
.field{height:50px;border-bottom:1px solid rgba(255,255,255,.35);color:var(--white);font-size:14px;display:flex;justify-content:space-between;align-items:center}
/* footer */
.footer{top:4236px;left:0;width:1200px;height:376px;background:linear-gradient(180deg,#fafafa,#eef0ea)}
.foot-nav{top:4457px;left:0;width:1200px;display:flex;justify-content:center;gap:50px;font-size:14px;color:#333}
</style>
</head>
<body>

<!-- header -->
<div class="abs topbar"></div>
<div class="abs brand-badge"></div>
<div class="abs brand-mark circle"></div>
<div class="abs brand-name">HARBORLINE LENDING AND CAPITAL OF FLORIDA<span>BUSINESS AND COMMERCIAL DIVISION</span></div>
<div class="abs" style="left:322px;top:34px;font-size:9px;color:#555">FOLLOW US ON:</div>
<div class="abs" style="left:420px;top:22px">
  <span class="social" aria-label="Social link one"></span><span class="social dark" aria-label="Social link two"></span><span class="social" aria-label="Social link three"></span>
</div>
<div class="abs" style="left:573px;top:12px;width:1px;height:60px;background:#ddd"></div>
<div class="abs circle" style="left:605px;top:22px;width:38px;height:38px;background:var(--forest)">
  <svg width="16" height="16" viewBox="0 0 24 24" fill="#fff"><path d="M6.6 10.8a15 15 0 0 0 6.6 6.6l2.2-2.2c.3-.3.7-.4 1-.2 1.1.4 2.3.6 3.6.6.6 0 1 .4 1 1V20c0 .6-.4 1-1 1A17 17 0 0 1 3 4c0-.6.4-1 1-1h3.5c.6 0 1 .4 1 1 0 1.3.2 2.5.6 3.6.1.3 0 .7-.2 1z"/></svg>
</div>
<div class="abs contact-mini" style="left:662px;top:24px">CALL US:<b>+1 888 555 0142</b></div>
<div class="abs" style="left:838px;top:12px;width:1px;height:60px;background:#ddd"></div>
<div class="abs circle" style="left:868px;top:22px;width:38px;height:38px;background:var(--forest)">
  <svg width="16" height="16" viewBox="0 0 24 24" fill="#fff"><path d="M2 6l10 7 10-7v12H2z"/><path d="M2 5h20l-10 7z"/></svg>
</div>
<div class="abs contact-mini" style="left:925px;top:24px">EMAIL US:<b style="font-size:18px">info@harborline.example</b></div>
<nav class="abs nav">
  <a href="#" class="current">HOME</a><a href="#">ABOUT US</a><a href="#">PROPERTIES</a><a href="#">BLOG</a><a href="#">CONTACT US</a>
</nav>

<!-- hero -->
<section class="abs hero">
  <div class="abs hero-photo" role="img" aria-label="Photo of smiling clients shaking hands with a loan officer across an office desk"></div>
  <div class="abs hero-label">RESIDENTIAL HOME LOANS IN FLORIDA &amp; COMMERCIAL LENDING IN AMERICA</div>
  <h1>BEST RESOURCE</h1>
  <h2>FOR HASSLE-FREE</h2>
  <h3>LOW COST MORTGAGE ORIGINATION</h3>
  <a class="abs hero-cta" href="#">FILL OUT MORTGAGE APPLICATION TO BEGIN LENDING PR</a>
</section>
<div class="abs scroll-bump"></div>
<svg class="abs" style="left:590px;top:646px" width="20" height="34" viewBox="0 0 20 34"><rect x="2" y="1" width="16" height="30" rx="8" fill="none" stroke="#666" stroke-width="2"/><path d="M10 8v14M6 18l4 4 4-4" stroke="#666" stroke-width="2" fill="none"/></svg>

<!-- about -->
<div class="abs vline" style="left:162px;top:743px;height:117px"></div>
<h2 class="abs sec-title" style="left:210px;top:748px">HELPING YOU OPEN THE DOOR TO<br>YOUR NEW HOME</h2>
<div class="abs eyebrow" style="left:210px;top:848px;font-size:15px">SEAMLESS FINANCING FOR YOUR NEW HOME</div>
<div class="abs photo" role="img" aria-label="Photo of a happy family sitting on the floor holding a cardboard roof over their heads" style="left:111px;top:904px;width:489px;height:651px;background:linear-gradient(160deg,#d9d2c6,#a89a87 50%,#6e6253);z-index:2;box-shadow:0 10px 30px rgba(0,0,0,.15)"></div>
<div class="abs about-text">
  <p>Harborline Originates Residential Home loans in Florida and Commercial and business financing in all 50 States. We have over 25 years of experience in ALL types of real estate and commercial lending.</p>
  <p>We are strategically partnered to help you obtain ALL necessary components of residential and commercial lending. From the RIGHT lending partners to the best practice Insurance avenues and commercial and residential real estate partners.</p>
  <ul class="ticks">
    <li><span class="tick"></span>Achieving Homeownership</li>
    <li><span class="tick"></span>Building Equity &amp; Tax Benefits</li>
    <li><span class="tick"></span>Fixed Monthly Payments</li>
    <li><span class="tick"></span>Long-Term Investment</li>
  </ul>
</div>
<a class="abs btn-dark" href="#" style="left:663px;top:1365px;width:143px;height:43px">Read More</a>

<!-- products -->
<section class="abs products">
  <div class="abs vline" style="left:1086px;top:-157px;height:242px"></div>
  <h2 class="abs sec-title" style="left:0;width:1200px;top:124px;text-align:center;color:var(--forest-deep)">WE OFFER ALL MORTGAGE LENDING PRODUCTS</h2>
  <div class="abs eyebrow" style="left:0;width:1200px;top:182px;text-align:center;color:#fff">OUR LOAN PROGRAMS</div>
  <p class="abs" style="left:180px;width:840px;top:222px;text-align:center;color:#fff;font-size:16px;line-height:30px">Sed ut perspiciatis unde omnis iste natus error sit voluptatem accusantium doloremque laudantium, totam rem aperiam, eaque ipsa quae ab illo inventore veritatis et quasi architecto</p>

  <div class="abs card" style="left:111px;top:307px">
    <svg width="44" height="44" viewBox="0 0 44 44" fill="none" stroke="#fff" stroke-width="2"><path d="M4 22L22 6l18 16M9 18v20h18"/><circle cx="31" cy="31" r="8"/><path d="M28 34l6-6"/></svg>
    <h4>Fixed-Rate Mortgages</h4><p>Ut enim ad minima veniam, quis nostrum exercitationem ullam corporis suscipit laboriosam.</p></div>
  <div class="abs card active" style="left:444px;top:307px">
    <svg width="44" height="44" viewBox="0 0 44 44" fill="none" stroke="#6e9a22" stroke-width="2"><path d="M4 22L22 6l18 16M9 18v20h26V18"/><path d="M17 30l10-10"/><circle cx="18" cy="21" r="2"/><circle cx="26" cy="29" r="2"/></svg>
    <h4>Adjustable-Rate Mortgages</h4><p>Ut enim ad minima veniam, quis nostrum exercitationem ullam corporis suscipit laboriosam.</p></div>
  <div class="abs card" style="left:776px;top:307px">
    <svg width="44" height="44" viewBox="0 0 44 44" fill="none" stroke="#fff" stroke-width="2"><path d="M6 14L22 6l16 8H6zM10 14v8M34 14v8"/><circle cx="22" cy="30" r="9"/><path d="M22 25v10"/></svg>
    <h4>Jumbo Loans</h4><p>Ut enim ad minima veniam, quis nostrum exercitationem ullam corporis suscipit laboriosam.</p></div>
  <div class="abs card" style="left:111px;top:545px">
    <svg width="44" height="44" viewBox="0 0 44 44" fill="none" stroke="#fff" stroke-width="2"><circle cx="28" cy="14" r="9"/><path d="M24 18l8-8"/><path d="M6 40V28h6v12M14 40V24h6v16M22 40V30h6v10"/></svg>
    <h4>Interest-Only Mortgages</h4><p>Ut enim ad minima veniam, quis nostrum exercitationem ullam corporis suscipit laboriosam.</p></div>
  <div class="abs card" style="left:444px;top:545px">
    <svg width="44" height="44" viewBox="0 0 44 44" fill="none" stroke="#fff" stroke-width="2"><path d="M6 40V18L22 6l16 12v22z"/><path d="M15 28h14M15 34h14M22 14v8"/></svg>
    <h4>Reverse Mortgages</h4><p>Ut enim ad minima veniam, quis nostrum exercitationem ullam corporis suscipit laboriosam.</p></div>
  <div class="abs card" style="left:776px;top:545px">
    <svg width="44" height="44" viewBox="0 0 44 44" fill="none" stroke="#fff" stroke-width="2"><path d="M8 40V20h14v20M22 40V8h14v32"/><path d="M12 26h6M12 32h6M26 14h6M26 20h6M26 26h6"/></svg>
    <h4>Construction Loans</h4><p>Ut enim ad minima veniam, quis nostrum exercitationem ullam corporis suscipit laboriosam.</p></div>
</section>

<!-- rates -->
<div class="abs" style="left:380px;top:2405px;width:140px;height:240px;background:var(--lime)"></div>
<div class="abs photo" role="img" aria-label="Photo of a modern house with a pool and wooden facade" style="left:111px;top:2405px;width:278px;height:380px;background:linear-gradient(180deg,#9ec3e6,#dfe3e4 45%,#4a8fb3 85%)"></div>
<div class="abs photo" role="img" aria-label="Photo of a dark modern building entrance with trees" style="left:412px;top:2405px;width:188px;height:213px;background:linear-gradient(180deg,#dfe6ea,#2a2a2a 50%,#111)"></div>
<div class="abs photo" role="img" aria-label="Photo of a suburban home with garage and pine trees" style="left:412px;top:2645px;width:188px;height:217px;background:linear-gradient(180deg,#6aa0e0,#6d8a5a 55%,#b8b2a8)"></div>
<div class="abs circle" style="left:111px;top:2812px;width:52px;height:52px;background:var(--forest)">
  <svg width="18" height="18" viewBox="0 0 24 24" fill="#fff"><path d="M6.6 10.8a15 15 0 0 0 6.6 6.6l2.2-2.2c.3-.3.7-.4 1-.2 1.1.4 2.3.6 3.6.6.6 0 1 .4 1 1V20c0 .6-.4 1-1 1A17 17 0 0 1 3 4c0-.6.4-1 1-1h3.5c.6 0 1 .4 1 1 0 1.3.2 2.5.6 3.6.1.3 0 .7-.2 1z"/></svg>
</div>
<div class="abs contact-mini" style="left:188px;top:2818px">CALL US:<b style="font-size:24px">+1 888 555 0142</b></div>

<h2 class="abs sec-title" style="left:657px;top:2396px">AFFORDABLE RATES FOR<br>EVERY BUDGET</h2>
<div class="abs eyebrow" style="left:657px;top:2497px">MORTGAGE INTEREST RATES</div>
<div class="abs rate-icon circle" style="left:657px;top:2543px"><svg width="28" height="28" viewBox="0 0 28 28" fill="none" stroke="#fff" stroke-width="2"><rect x="5" y="4" width="16" height="20"/><path d="M9 10h8M9 15h8"/><circle cx="21" cy="21" r="4"/></svg></div>
<div class="abs rate-num" style="left:747px;top:2547px">58<sup>%</sup></div>
<div class="abs rate-label" style="left:747px;top:2588px">FIXED-RATE MORTGAGES</div>
<p class="abs rate-copy" style="left:657px;top:2624px">Ad minima veniam, quis nostrum exercitationem ullam corporis suscipit laboriosam nisi ut aliquid ex ea commodi consequatur?</p>
<div class="abs rate-icon circle" style="left:657px;top:2728px"><svg width="28" height="28" viewBox="0 0 28 28" fill="none" stroke="#fff" stroke-width="2"><rect x="5" y="4" width="16" height="20"/><path d="M9 10h8M9 15h8"/><path d="M18 20l6 6"/></svg></div>
<div class="abs rate-num" style="left:747px;top:2732px">85<sup>%</sup></div>
<div class="abs rate-label" style="left:747px;top:2773px">ADJUSTABLE-RATE MORTGAGES (ARMS)</div>
<p class="abs rate-copy" style="left:657px;top:2810px">Ad minima veniam, quis nostrum exercitationem ullam corporis suscipit laboriosam nisi ut aliquid</p>

<!-- properties -->
<div class="abs vline" style="left:110px;top:2901px;height:197px;z-index:2"></div>
<section class="abs properties">
  <h2 class="abs sec-title" style="left:0;width:1200px;top:65px;text-align:center">WHERE YOUR JOURNEY BEGINS</h2>
  <div class="abs eyebrow" style="left:0;width:1200px;top:120px;text-align:center">AVAILABLE PROPERTIES</div>
  <div class="abs prop" style="left:98px;top:170px;background:linear-gradient(180deg,#c9ccd0,#f2f2f2 35%,#3a3a3a 70%,#6b6b6b)" role="img" aria-label="Photo of a white modern house with balcony">
    <div class="prop-tag"><span class="pin-box"><svg width="16" height="20" viewBox="0 0 16 20" fill="#173d17"><path d="M8 0a8 8 0 0 1 8 8c0 6-8 12-8 12S0 14 0 8a8 8 0 0 1 8-8zm0 5a3 3 0 1 0 0 6 3 3 0 0 0 0-6z"/></svg></span><div><b>12 TIDEWATER LANE</b><a href="#">View Details</a></div></div>
  </div>
  <div class="abs prop" style="left:442px;top:170px;background:linear-gradient(180deg,#6d8eb0,#2b3038 40%,#1c1d20 70%,#8a5a2c)" role="img" aria-label="Photo of a dark modern house lit at dusk">
    <div class="prop-tag light"><span class="pin-box"><svg width="16" height="20" viewBox="0 0 16 20" fill="#173d17"><path d="M8 0a8 8 0 0 1 8 8c0 6-8 12-8 12S0 14 0 8a8 8 0 0 1 8-8zm0 5a3 3 0 1 0 0 6 3 3 0 0 0 0-6z"/></svg></span><div><b>34 MARLOW AVENUE</b><a href="#">View Details</a></div></div>
  </div>
  <div class="abs prop" style="left:784px;top:170px;background:linear-gradient(90deg,#8b4a3a,#a05c48 55%,#5c87c7)" role="img" aria-label="Photo of a modern building with red timber cladding against blue sky">
    <div class="prop-tag"><span class="pin-box"><svg width="16" height="20" viewBox="0 0 16 20" fill="#173d17"><path d="M8 0a8 8 0 0 1 8 8c0 6-8 12-8 12S0 14 0 8a8 8 0 0 1 8-8zm0 5a3 3 0 1 0 0 6 3 3 0 0 0 0-6z"/></svg></span><div><b>78 CYPRESS BOULEVARD</b><a href="#">View Details</a></div></div>
  </div>
  <div class="abs arrow-btn circle" style="left:37px;top:368px;background:#cfd4c3"><svg width="12" height="12" viewBox="0 0 12 12"><path d="M8 2L4 6l4 4" stroke="#fff" stroke-width="2" fill="none"/></svg></div>
  <div class="abs arrow-btn circle" style="left:1129px;top:368px;background:var(--forest)"><svg width="12" height="12" viewBox="0 0 12 12"><path d="M4 2l4 4-4 4" stroke="#fff" stroke-width="2" fill="none"/></svg></div>
</section>

<!-- contact -->
<section class="abs contact">
  <h2 class="abs sec-title" style="left:0;width:1200px;top:55px;text-align:center;color:#fff">GET IN TOUCH WITH US</h2>
  <div class="abs eyebrow" style="left:0;width:1200px;top:104px;text-align:center;color:#fff">JOIN WITH US</div>
  <div class="abs field" style="left:251px;top:148px;width:313px">First Name *<svg width="12" height="12" viewBox="0 0 12 12" fill="#fff"><circle cx="6" cy="3.5" r="3"/><path d="M0 12c0-4 3-5 6-5s6 1 6 5z"/></svg></div>
  <div class="abs field" style="left:636px;top:148px;width:313px">Last Name *<svg width="12" height="12" viewBox="0 0 12 12" fill="#fff"><circle cx="6" cy="3.5" r="3"/><path d="M0 12c0-4 3-5 6-5s6 1 6 5z"/></svg></div>
  <div class="abs field" style="left:251px;top:216px;width:313px">Email Address *<svg width="13" height="10" viewBox="0 0 13 10" fill="#fff"><path d="M0 0h13L6.5 5z"/><path d="M0 2l6.5 5L13 2v8H0z"/></svg></div>
  <div class="abs field" style="left:636px;top:216px;width:313px">Contact Number *<svg width="12" height="12" viewBox="0 0 24 24" fill="#fff"><path d="M6.6 10.8a15 15 0 0 0 6.6 6.6l2.2-2.2c.3-.3.7-.4 1-.2 1.1.4 2.3.6 3.6.6.6 0 1 .4 1 1V20c0 .6-.4 1-1 1A17 17 0 0 1 3 4c0-.6.4-1 1-1h3.5c.6 0 1 .4 1 1 0 1.3.2 2.5.6 3.6.1.3 0 .7-.2 1z"/></svg></div>
  <div class="abs field" style="left:251px;top:284px;width:698px;height:164px;align-items:flex-start;padding-top:16px">Comments *<svg width="13" height="12" viewBox="0 0 13 12" fill="#fff"><path d="M1 1h11v7H5l-3 3V8H1z"/></svg></div>
  <a class="abs btn-dark" href="#" style="left:527px;top:469px;width:143px;height:43px;background:#fff;color:var(--forest)">Submit</a>
</section>

<!-- footer -->
<footer class="abs footer"></footer>
<div class="abs circle" style="left:390px;top:4282px;width:120px;height:120px;background:var(--forest)"></div>
<div class="abs brand-name" style="left:530px;top:4330px">HARBORLINE LENDING AND CAPITAL OF FLORIDA<span>BUSINESS AND COMMERCIAL DIVISION</span></div>
<div class="abs foot-nav"><span>HOME</span><span>|</span><span>ABOUT US</span><span>|</span><span>PROPERTIES</span><span>|</span><span style="margin-left:60px">CONTACT US</span></div>
<div class="abs" style="left:486px;top:4514px;font-size:9px;color:#555">FOLLOW US ON:</div>
<div class="abs" style="left:584px;top:4502px">
  <span class="social" aria-label="Social link one"></span><span class="social dark" aria-label="Social link two"></span><span class="social" aria-label="Social link three"></span>
</div>
<div class="abs" style="left:111px;top:4565px;width:978px;height:1px;background:var(--lime)"></div>
<div class="abs" style="left:0;width:1200px;top:4586px;text-align:center;font-size:11px;color:#444">(C) COPYRIGHT | ALL RIGHTS RESERVED</div>

</body>
</html>
```